Business Name: DM Space Arranging Pty Ltd

Business Type: Professional Home Styling and Minor Renovation Business

Logo: Attached is the logo that has been created.
I always envisaged the logo in the middle of the business card with my full name underneath it.

Marnie Tulloch B.Com LMR HTV
Property Stylist & Project Manager

Include dot points of services
Staging Houses for Sale
Minor Home Renovations
Home Styling & Project Management
Re-Designing Living Spaces to Aid the Disabled

Somewhere on the card I would like to incorporate
"Property Styling and Cosmetic Renovations"

Colour Scheme:
Gloss black business card, with white and then
Gold or Silver as the highlight colours.

Incorporate a small amount of yellow only if possible to make it pop. If this really doesn’t work it doesn’t have to be used. Also l like the colour teal if that needs to be used as a contrast colour.

Feel/Themes
• I love antique chairs, regal expensive looking furniture mixed with modern homes (this is the unique style I want to sell) antique and modern mix that looks high class as well as modern and fresh, targeting an executive market.
• I want to use an orchid as a trademark throughout the course of my work, not sure if this can somehow be incorporated? Also really like crowns to give that regal/antique feel and then something else to give that modern twist (I don’t know what the something else could be)
• Wall Paper Look (on a portion of it not all of it, like a French look)
• Overall feel - A very deluxe and professional feel with a little bit of creative flare.

I hope this helps create a bit of a picture.

Is it ok that I call you tomorrow morning? My mobile number is 0438 926 574 if you have any questions for me in the meantime.

Target Market(s)

High Quality Executive Market - People selling homes

Industry/Entity Type

Business

Contact Information for Business Card

Include dot points of services:
Staging Houses for Sale
Minor Home Renovations

Font styles to use
Serif
Script

Colors
33b8a4
fbed22

Requirements
Must have
• Marnie Tulloch B.Com LMR HTV
• Property Stylist & Project Manager
• LMR and HTV Logos on the card
• "Dramatically increase the value of your property"
Nice to have
• Colour Scheme:
• Gloss black business card, with white and then
• Gold or Silver as the highlight colours.
• Incorporate a small amount of yellow only if possible to make it pop. If this really doesn’t work it doesn’t have to be used. Also l like the colour teal if that needs to be used as a contrast colour.
• Also like teal as a highlight colour.

```html
<!DOCTYPE html>
<html lang="en">
<head>
<meta charset="utf-8">
<title>DM Space Arranging Pty Ltd — Business Cards</title>
<link rel="stylesheet" href="https://fonts.googleapis.com/css2?family=Great+Vibes&family=Tinos:wght@400;700&display=swap">
<style>
  :root {
    --backdrop: #3b3b3d;
    --card: #ffffff;
    --ink: #1a1a1a;
    --black: #0d0d0d;
    --gold: #c9a13e;
    --gold-light: #ecd27e;
    --gold-dark: #8e6a1c;
    --white: #ffffff;
  }
  * { box-sizing: border-box; margin: 0; padding: 0; }
  html, body {
    width: 1200px; height: 852px; overflow: hidden;
    background: var(--backdrop);
  }
  .canvas { position: relative; width: 1200px; height: 852px; }

  .card {
    position: absolute; top: 266px;
    width: 545px; height: 320px;
    background: var(--card);
    border-radius: 12px;
    overflow: hidden;
    font-family: "Tinos", "Times New Roman", serif;
    color: var(--ink);
  }
  .card--front { left: 40px; }
  .card--back { left: 615px; }

  .card__art { position: absolute; inset: 0; width: 100%; height: 100%; }

  .ornament {
    position: absolute;
    background: radial-gradient(ellipse at center, #e6e6e6 0%, #f3f3f3 55%, rgba(255,255,255,0) 80%);
  }

  .wordmark {
    position: absolute;
    text-align: center;
    border-top: 1px solid var(--ink);
    border-bottom: 1px solid var(--ink);
    padding: 4px 0 3px;
    font-size: 11px;
    letter-spacing: 2px;
    text-transform: uppercase;
    color: var(--gold-dark);
    white-space: nowrap;
  }

  /* Front */
  .card--front .ornament { left: 110px; top: 20px; width: 320px; height: 110px; }
  .card--front .wordmark { left: 90px; top: 92px; width: 300px; }
  .accreditation {
    position: absolute; left: 410px; top: 78px;
    width: 110px; height: 46px;
    border: 1px solid var(--black);
    display: flex;
  }
  .accreditation__block { flex: 1; background: var(--black); }
  .accreditation__seal { width: 30px; margin: 8px; background: var(--gold); }

  .services {
    position: absolute; left: 28px; top: 164px;
    list-style: none;
    font-size: 14.5px; line-height: 22px;
  }
  .services li::before { content: "» "; }
  .services .pair span { margin-left: 10px; }

  /* Back */
  .card--back .ornament { left: 130px; top: 10px; width: 240px; height: 90px; }
  .card--back .wordmark { left: 140px; top: 66px; width: 222px; font-size: 10px; letter-spacing: 1.4px; }

  .person { position: absolute; left: 48px; top: 104px; }
  .person__name {
    font-family: "Great Vibes", cursive;
    font-size: 32px; font-weight: 400; line-height: 1;
    margin-bottom: 8px;
  }
  .person__role { font-size: 14px; line-height: 17px; padding-left: 18px; }

  .contact {
    position: absolute; left: 48px; top: 212px;
    list-style: none; font-size: 15px; line-height: 22px;
  }
  .contact li { display: flex; align-items: center; gap: 10px; }
  .contact svg { width: 13px; height: 13px; flex: none; }
  .icon--solid { fill: var(--ink); }
  .icon--line { fill: none; stroke: var(--ink); stroke-width: 1.5; }

  .tagline {
    position: absolute; left: 392px; top: 135px; width: 150px;
    color: var(--white); font-size: 13.5px; line-height: 18px; text-align: center;
  }
</style>
</head>
<body>
<main class="canvas">

  <section class="card card--front" aria-label="Business card front">
    <svg class="card__art" viewBox="0 0 545 320" aria-hidden="true">
      <defs>
        <linearGradient id="goldFront" x1="0" y1="1" x2="1" y2="0">
          <stop offset="0" stop-color="#8e6a1c"/>
          <stop offset="0.45" stop-color="#ecd27e"/>
          <stop offset="0.75" stop-color="#c9a13e"/>
          <stop offset="1" stop-color="#f3dc8f"/>
        </linearGradient>
      </defs>
      <path d="M0 320 L0 314 C160 306 330 264 545 214 L545 222 C390 258 260 300 200 320 Z" fill="#0d0d0d"/>
      <path d="M200 320 C260 300 390 258 545 222 L545 234 C410 266 300 300 255 320 Z" fill="url(#goldFront)"/>
    </svg>
    <div class="ornament" role="img" aria-label="Faint crown and scroll flourish behind the name"></div>
    <div class="wordmark">DM Space Arranging Pty Ltd</div>
    <div class="accreditation" role="img" aria-label="Accreditation badge">
      <span class="accreditation__block"></span>
      <span class="accreditation__seal"></span>
    </div>
    <ul class="services">
      <li class="pair">Staging Homes for Sale <span>» Minor Home Renovations</span></li>
      <li>Home Styling, Project &amp; Budget Management</li>
      <li>Source Furnishings &amp; Accessories</li>
      <li>Re-Designing Rooms for the Disabled</li>
    </ul>
  </section>

  <section class="card card--back" aria-label="Business card back">
    <svg class="card__art" viewBox="0 0 545 320" aria-hidden="true">
      <defs>
        <linearGradient id="goldBack" x1="0" y1="1" x2="1" y2="0">
          <stop offset="0" stop-color="#8e6a1c"/>
          <stop offset="0.4" stop-color="#ecd27e"/>
          <stop offset="0.7" stop-color="#b58a2c"/>
          <stop offset="1" stop-color="#ecd27e"/>
        </linearGradient>
      </defs>
      <path d="M412 0 H545 V320 H250 C330 290 365 210 382 130 C392 70 400 25 412 0 Z" fill="#0d0d0d"/>
      <path d="M0 312 C160 308 300 275 345 175 C370 110 382 45 398 0" fill="none" stroke="url(#goldBack)" stroke-width="5"/>
      <path d="M20 305 C170 296 290 262 330 180 C355 120 366 55 380 0" fill="none" stroke="url(#goldBack)" stroke-width="2"/>
      <path d="M0 320 H230 C180 318 110 316 0 316 Z" fill="url(#goldBack)"/>
    </svg>
    <div class="ornament" role="img" aria-label="Faint crown and scroll flourish behind the name"></div>
    <div class="wordmark">DM Space Arranging Pty Ltd</div>

    <div class="person">
      <h1 class="person__name">Marnie Tulloch</h1>
      <p class="person__role">B.Com LMR HTV<br>Property Stylist &amp;<br>Project Manager</p>
    </div>

    <ul class="contact">
      <li>
        <svg class="icon--solid" viewBox="0 0 16 16"><path d="M3 1h3l1.5 4-2 1.3a9 9 0 0 0 4.2 4.2L11 8.5l4 1.5v3a2 2 0 0 1-2 2A13 13 0 0 1 1 3a2 2 0 0 1 2-2z"/></svg>
        00 00 000 00 0
      </li>
      <li>
        <svg class="icon--line" viewBox="0 0 16 16"><path d="M1 3h14v10H1z M1 3l7 6 7-6"/></svg>
        yourname@yourwebsite.com
      </li>
      <li>
        <svg class="icon--line" viewBox="0 0 16 16"><circle cx="8" cy="8" r="6.5"/><path d="M1.5 8h13 M8 1.5c-3 3.5-3 9.5 0 13 M8 1.5c3 3.5 3 9.5 0 13"/></svg>
        www.yourwebsite.com
      </li>
    </ul>

    <p class="tagline">Dramatically Increase<br>the Value of Your Home</p>
  </section>

</main>
</body>
</html>
```